Push notification screens at app start up

We have an existing news publication app platform and are adding categories to push notifications.

We need two screens designed (each for Zorbel, Quillet and Android for a total of 6d) that show when the app is first launched.

The workflow of our app:
0. app launch screen while webservices run (no work needed)
1. information screen to the user promoting the benefits of push notification with "Next" button. (see concept attached)
2. Push categories selection screen. This will have list of category types, with on/off switch.

"Select the categories that you wish to receive occasional notices:
Breaking News (on/off switch)
Local News (on/off switch)
Sports (on/off switch)
Local Events (on/off switch)
Weather Alerts (on/off switch)
Local Deals (on/off switch)"

"Enable these categories on the next screen."
"Next" button

Background:
When I was looking around at app designs, I came across this one (http://www.plinthworks.example/design/7719034) and I really liked it. We obviously have different features on our screen, but I’d like to have this same feel. The colors used in this design are perfect.

UPDATE: I do not mean to limit your design to match the layout as the one mentioned above. Please use your creativity for the layout.

Our standard font in Helvetica Neue.

Notes:
- our app is developed for all phone devices from Zorbel 4 to Zorbel 6, so designs should be thoughtful of vertical scrolling if needed.
- our app is developed for Quillets, so we'll need designs completed as well. (We can finalize Zorbel design first, then translate the design to Quillet.)
- our app is developed for Android phones (not tablets), so we'll need designs completed as well. (We can finalize iOS design first, then translater to Android UI design guidelines).

We hope to establish a good on-going relationship with the designer for as-needed work in the future.

News

• Helvetica Neue

• Clean designs. No clutter.
• We would likely go with the standard on/off switches for both iOS and Android, but are open to small custom variations.

```html
<!DOCTYPE html>
<html lang="en">
<head>
<meta charset="utf-8">
<title>Notifications – Onboarding Screen</title>
<link rel="stylesheet" href="https://fonts.googleapis.com/css2?family=Arimo:wght@400;700&display=swap">
<style>
  :root {
    --screen-bg: #ffffff;
    --card-bg: #e1e1e1;
    --card-border: #bcbcbc;
    --accent-blue: #2c7cf6;
    --ink: #111111;
    --status-ink: #1a1a1a;
    --on-accent: #ffffff;
  }
  * { box-sizing: border-box; margin: 0; padding: 0; }
  html, body {
    width: 675px;
    height: 1200px;
    overflow: hidden;
    background: var(--screen-bg);
  }
  body {
    font-family: "Arimo", "Helvetica Neue", Helvetica, Arial, sans-serif;
    color: var(--ink);
    position: relative;
  }

  /* Status bar */
  .status-bar {
    position: absolute;
    top: 0; left: 0;
    width: 675px;
    height: 52px;
    font-size: 19px;
    color: var(--status-ink);
  }
  .status-bar .signal {
    position: absolute;
    left: 10px; top: 21px;
    display: flex;
    gap: 4px;
  }
  .status-bar .signal span {
    width: 11px; height: 11px;
    border-radius: 50%;
    border: 1.5px solid var(--status-ink);
  }
  .status-bar .signal span.on { background: var(--status-ink); }
  .status-bar .carrier { position: absolute; left: 76px; top: 16px; }
  .status-bar .wifi { position: absolute; left: 168px; top: 16px; }
  .status-bar .clock {
    position: absolute; left: 0; right: 0; top: 16px;
    text-align: center; font-weight: 700;
  }
  .status-bar .battery-level { position: absolute; left: 555px; top: 16px; }
  .status-bar .battery { position: absolute; left: 608px; top: 18px; }

  /* Info card */
  .info-card {
    position: absolute;
    left: 27px; top: 207px;
    width: 621px; height: 659px;
    background: var(--card-bg);
    border: 2px solid var(--card-border);
    border-radius: 22px;
    text-align: center;
  }
  .info-badge {
    position: absolute;
    left: 234px; top: 95px;
    width: 206px; height: 206px;
    border-radius: 50%;
    background: var(--accent-blue);
    display: flex; align-items: center; justify-content: center;
  }
  .info-title {
    position: absolute;
    left: 0; right: 0; top: 138px;
    font-size: 43px;
    font-weight: 700;
    letter-spacing: -0.3px;
  }
  .info-copy {
    position: absolute;
    left: 0; right: 0;
    font-size: 24.5px;
    line-height: 34px;
  }
  .info-copy.lead { top: 224px; }
  .info-copy.note { top: 476px; }

  /* Primary action */
  .next-button {
    position: absolute;
    left: 27px; top: 916px;
    width: 621px; height: 99px;
    border: none;
    border-radius: 11px;
    background: var(--accent-blue);
    color: var(--on-accent);
    font-family: inherit;
    font-size: 42px;
    font-weight: 700;
    letter-spacing: 0.5px;
  }
</style>
</head>
<body>
  <header class="status-bar">
    <div class="signal"><span class="on"></span><span class="on"></span><span class="on"></span><span></span><span></span></div>
    <span class="carrier">KESTREL</span>
    <svg class="wifi" width="26" height="20" viewBox="0 0 26 20" aria-hidden="true">
      <path d="M13 18 L9 13.5 A6 6 0 0 1 17 13.5 Z" fill="var(--status-ink)"/>
      <path d="M5.5 10 A11 11 0 0 1 20.5 10" stroke="var(--status-ink)" stroke-width="2.6" fill="none"/>
      <path d="M2 6.5 A16 16 0 0 1 24 6.5" stroke="var(--status-ink)" stroke-width="2.6" fill="none"/>
    </svg>
    <span class="clock">4:21 PM</span>
    <span class="battery-level">100%</span>
    <svg class="battery" width="54" height="20" viewBox="0 0 54 20" aria-hidden="true">
      <rect x="1" y="1" width="47" height="18" rx="3" fill="none" stroke="var(--status-ink)" stroke-width="1.6"/>
      <rect x="3.5" y="3.5" width="42" height="13" rx="1.5" fill="var(--status-ink)"/>
      <rect x="49.5" y="6.5" width="3" height="7" rx="1" fill="var(--status-ink)"/>
    </svg>
  </header>

  <section class="info-card">
    <h1 class="info-title">Notifications</h1>
    <p class="info-copy lead">By enabling push notifications, you can<br>keep up to date with occasional<br>notifications related to items you care<br>about. Select the categories on the<br>next screen and then authorize the<br>push notifications.</p>
    <p class="info-copy note">If you ever change your mind, you can<br>adjust these options in the Settings<br>menu of this app.</p>
  </section>

  <div class="info-badge" style="left:234px; top:95px;">
    <svg width="120" height="100" viewBox="0 0 120 100" aria-hidden="true" fill="none" stroke="var(--on-accent)" stroke-width="6" stroke-linejoin="round" stroke-linecap="round">
      <path d="M10 36 H36 L72 14 V78 L36 58 H10 Z"/>
      <path d="M36 36 V58"/>
      <path d="M24 58 L30 86 H42 L38 58"/>
      <path d="M84 36 A14 14 0 0 1 84 58"/>
      <path d="M94 26 A28 28 0 0 1 94 68"/>
    </svg>
  </div>

  <button class="next-button" type="button">NEXT</button>
</body>
</html>
```